Restyle corporate identity (+ logo) for a road construction company

We need a new logo and stationary design for our company VARNOK path. VARNOK path® increases the road base strength, while reducing major costs and time of road construction. Attached some examples of the current design.

Our wishes for the new logo:
- Business look
- Style sheet
- Modern

More information: www.varnokpath.example
Updates

Target Market(s)

Government

Industry/Entity Type

Construction

Requirements
Must have
• Logo (with road sign) + text

```html
<!DOCTYPE html>
<html lang="en">
<head>
<meta charset="utf-8">
<title>VARNOK path – Business Card</title>
<link rel="stylesheet" href="https://fonts.googleapis.com/css2?family=Open+Sans:wght@400;600;700&display=swap">
<style>
  :root {
    --brand-blue: #0a7ae2;
    --paper-grey: #e4e5e9;
    --backdrop: #8e8e8e;
    --ink-white: #ffffff;
    --ink-soft: #eaf3fd;
  }
  * { margin: 0; padding: 0; box-sizing: border-box; }
  html, body {
    width: 1105px;
    height: 1200px;
    overflow: hidden;
    background: var(--backdrop);
    font-family: "Open Sans", Arial, sans-serif;
  }
  .stage { position: relative; width: 1105px; height: 1200px; }

  .card {
    position: absolute;
    left: 182px;
    width: 747px;
    height: 426px;
    box-shadow: 0 10px 18px rgba(0,0,0,0.28);
  }
  .card--front { top: 119px; display: flex; }
  .card--back  { top: 637px; background: var(--brand-blue); }

  .contact-panel {
    width: 350px;
    height: 100%;
    background: var(--brand-blue);
    color: var(--ink-white);
    padding: 50px 0 0 50px;
    position: relative;
  }
  .person-name {
    font-weight: 600;
    font-size: 24px;
    letter-spacing: 0.3px;
    line-height: 1.1;
  }
  .person-role {
    font-size: 19px;
    color: var(--ink-soft);
    margin-top: 4px;
  }
  .address {
    position: absolute;
    top: 200px;
    left: 50px;
    font-style: normal;
    font-size: 19px;
    line-height: 27px;
    color: var(--ink-soft);
  }
  .contact-list {
    position: absolute;
    top: 296px;
    left: 50px;
    list-style: none;
    font-size: 19px;
    line-height: 28px;
    color: var(--ink-soft);
  }
  .contact-list li { display: flex; align-items: center; gap: 9px; }
  .contact-list svg { width: 17px; height: 17px; flex: none; }

  .brand-panel {
    flex: 1;
    background: var(--paper-grey);
    display: flex;
    align-items: center;
    justify-content: center;
    border-left: 3px solid #c9ccd2;
  }
  .brand-name {
    font-weight: 700;
    font-size: 44px;
    color: var(--brand-blue);
    letter-spacing: 1px;
  }

  .back-name {
    position: absolute;
    top: 150px;
    left: 0;
    width: 100%;
    text-align: center;
    font-weight: 700;
    font-size: 58px;
    color: var(--paper-grey);
    letter-spacing: 1px;
  }
  .back-url {
    position: absolute;
    top: 355px;
    left: 0;
    width: 100%;
    text-align: center;
    font-size: 19px;
    letter-spacing: 6px;
    color: var(--ink-soft);
  }
</style>
</head>
<body>
<main class="stage">
  <section class="card card--front">
    <div class="contact-panel">
      <h1 class="person-name">LENA VORST</h1>
      <p class="person-role">CEO/Founder</p>
      <address class="address">
        Lindenkade 58<br>
        2511 KT The Hague<br>
        The Netherlands
      </address>
      <ul class="contact-list">
        <li>
          <svg viewBox="0 0 16 16" aria-hidden="true"><path fill="#fff" d="M3.6 1.2l2.3 2.9-1.3 1.6c.9 2 2.4 3.6 4.4 4.6l1.6-1.3 2.9 2.3-1.3 2.3C7 13.4 2.6 9 1.3 2.5z"/></svg>
          555 014 2290
        </li>
        <li>
          <svg viewBox="0 0 16 16" aria-hidden="true"><rect x="1" y="3.5" width="14" height="9.5" fill="#fff"/><path d="M1.5 4l6.5 5 6.5-5" fill="none" stroke="#0a7ae2" stroke-width="1.2"/></svg>
          info@varnokpath.example
        </li>
        <li>
          <svg viewBox="0 0 16 16" aria-hidden="true"><circle cx="8" cy="8" r="7" fill="#fff"/><path d="M8 1v14M1 8h14M3 4.2c3 1.4 7 1.4 10 0M3 11.8c3-1.4 7-1.4 10 0" stroke="#0a7ae2" stroke-width="1" fill="none"/></svg>
          www.varnokpath.example
        </li>
      </ul>
    </div>
    <div class="brand-panel">
      <span class="brand-name">VARNOK path</span>
    </div>
  </section>

  <section class="card card--back">
    <p class="back-name">VARNOK path</p>
    <p class="back-url">www.varnokpath.example</p>
  </section>
</main>
</body>
</html>
```